Veltrano.co - Polar Expeditions Specialists

We need a modern, visually striking business card for Veltrano.co, a company specialized in selling expedition cruises to the most remote regions on Earth, with a focus on the Arctic and Antarctica. The design should instantly communicate that the cardholder is an expert in polar travel. Use clean, premium aesthetics with cool tones like icy blue and white, possibly incorporating polar imagery (ice, glaciers, penguins, etc.)

Attached the logo

Contact Information for Business Card

Feels high-end and trustworthy.. Visually memorable — encourages people to keep it

Colors
0054AA
0677BA
7BADD7
CADEEF
E8F1F8

Requirements
Must have
• ice, glaciers, penguins, montains
Nice to have
• modern, transparente,

```html
<!DOCTYPE html>
<html lang="en">
<head>
<meta charset="utf-8">
<title>Veltrano.co – Business Card</title>
<link rel="stylesheet" href="https://fonts.googleapis.com/css2?family=Poppins:wght@400;600;700&display=swap">
<style>
  :root {
    --backdrop: #2b2b2e;
    --card-light: #ffffff;
    --card-dark: #0b0b2b;
    --brand-blue: #3a78c2;
    --ink: #2a2a2a;
    --on-dark: #ffffff;
  }
  * { margin: 0; padding: 0; box-sizing: border-box; }
  html, body { width: 1200px; height: 1195px; overflow: hidden; }
  body {
    background: var(--backdrop);
    font-family: "Poppins", sans-serif;
    position: relative;
  }
  .card {
    position: absolute;
    top: 248px;
    width: 420px;
    height: 700px;
    border-radius: 28px;
    display: flex;
    flex-direction: column;
    align-items: center;
    text-align: center;
    box-shadow: 0 12px 30px rgba(0,0,0,.45);
  }
  .card--front { left: 150px; background: var(--card-light); color: var(--ink); padding-top: 78px; }
  .card--back { left: 630px; background: var(--card-dark); color: var(--on-dark); justify-content: center; padding-bottom: 20px; }

  .brand { display: flex; flex-direction: column; align-items: center; }
  .brand__mark {
    width: 86px; height: 86px; border-radius: 50%;
    background: var(--brand-blue);
    margin-bottom: 14px;
  }
  .card--back .brand__mark { background: var(--on-dark); }
  .brand__name {
    font-size: 54px; font-weight: 700; line-height: 1;
    color: var(--brand-blue); letter-spacing: -0.5px;
  }
  .card--back .brand__name { color: var(--on-dark); }
  .brand__tagline {
    font-size: 18px; font-weight: 600; margin-top: 6px;
    color: var(--brand-blue);
  }
  .card--back .brand__tagline { color: var(--on-dark); }

  .holder { margin-top: 78px; }
  .holder__name { font-size: 27px; font-weight: 600; color: var(--brand-blue); line-height: 1.2; }
  .holder__role { font-size: 15px; font-weight: 400; color: var(--ink); }

  .icon-row { display: flex; align-items: center; gap: 8px; margin-top: 22px; }
  .icon-row__rule { width: 28px; height: 1.5px; background: var(--brand-blue); }
  .icon { width: 22px; height: 22px; }

  .contact { margin-top: 12px; font-size: 16px; line-height: 1.45; }
  .divider { width: 80px; height: 1.5px; background: var(--brand-blue); margin: 16px 0 14px; }
  .address { font-size: 16px; line-height: 1.45; }
</style>
</head>
<body>
  <section class="card card--front">
    <div class="brand">
      <div class="brand__mark"></div>
      <div class="brand__name">Veltrano.co</div>
      <div class="brand__tagline">Polar Expeditions Specialists</div>
    </div>

    <div class="holder">
      <div class="holder__name">Marlo Kessing</div>
      <div class="holder__role">CEO &amp; Founder</div>
    </div>

    <div class="icon-row">
      <span class="icon-row__rule"></span>
      <svg class="icon" viewBox="0 0 22 22" aria-label="Phone">
        <rect width="22" height="22" rx="5" fill="#3a78c2"/>
        <path d="M7 5.5l2 .3 1 3-1.5 1.2a8 8 0 0 0 3.5 3.5L13.2 12l3 1 .3 2c0 .8-.7 1.5-1.5 1.5A10 10 0 0 1 5.5 7c0-.8.7-1.5 1.5-1.5z" fill="#fff"/>
      </svg>
      <svg class="icon" viewBox="0 0 22 22" aria-label="Email">
        <rect width="22" height="22" rx="5" fill="#3a78c2"/>
        <rect x="5" y="7" width="12" height="8.5" rx="1" fill="#fff"/>
        <path d="M5.5 7.5L11 12l5.5-4.5" stroke="#3a78c2" stroke-width="1.2" fill="none"/>
      </svg>
      <svg class="icon" viewBox="0 0 22 22" aria-label="Website">
        <rect width="22" height="22" rx="5" fill="#3a78c2"/>
        <circle cx="11" cy="11" r="6" fill="none" stroke="#fff" stroke-width="1.3"/>
        <ellipse cx="11" cy="11" rx="2.6" ry="6" fill="none" stroke="#fff" stroke-width="1.1"/>
        <path d="M5 11h12" stroke="#fff" stroke-width="1.1"/>
      </svg>
      <span class="icon-row__rule"></span>
    </div>

    <div class="contact">
      <div>+1.555.010.2040</div>
      <div>hello@veltrano.co</div>
      <div>www.veltrano.co</div>
    </div>
    <div class="divider"></div>
    <div class="address">
      <div>48 Harbor Crest Lane</div>
      <div>Easton Ridge, ME 04012 USA</div>
    </div>
  </section>

  <section class="card card--back">
    <div class="brand">
      <div class="brand__mark"></div>
      <div class="brand__name">Veltrano.co</div>
      <div class="brand__tagline">Polar Expeditions Specialists</div>
    </div>
  </section>
</body>
</html>
```